Remodeling brochure

We need an informative homeowner friendly brochure detailing our company and things we do. We are looking for an initial setup and ideas (# of pages, etc) and then we will send more content. We are uploading our logo design. We are a high end remodeling company specializing in kitchen & bath remodels. We sell ourselves on customer communication and attention to detail in our designs and remodels.

Target Market(s)

Residential homeowners

Contact Information for Business Card

Modern and attention grabbing

Requirements
Must have
• Name- Hearth & Tile Works<br/>Address- 718 NW Larkfield Drive Suite #207<br/> Ankeny, Iowa 50099<br/>Phone- 515-555-0184<br/>email-htworksiowa@example-mail.com

```html
<!DOCTYPE html>
<html lang="en">
<head>
<meta charset="utf-8">
<title>Hearth &amp; Tile Works — Remodeling Brochure</title>
<link rel="stylesheet" href="https://fonts.googleapis.com/css2?family=Anton&family=Montserrat:ital,wght@0,300;0,400;0,500;0,600;0,700;1,700;1,800&family=Oswald:wght@600;700&display=swap">
<style>
  :root {
    --stage: #a6a6a6;
    --paper: #ffffff;
    --brand-blue: #2a87d0;
    --quote-indigo: #3b5ab6;
    --ink: #1b1b1b;
    --rule: #c9d9ea;
    --photo-kitchen: linear-gradient(160deg, #cfcac1 0%, #e9e4da 40%, #b9ac97 75%, #7d6a55 100%);
    --photo-grey-kitchen: linear-gradient(150deg, #e8e8e6 0%, #9a9b9d 45%, #4c4f55 100%);
    --photo-bath: linear-gradient(155deg, #f4f4f2 0%, #dcdde0 40%, #6b6f78 75%, #45484f 100%);
    --photo-open-kitchen: linear-gradient(160deg, #f2f1ee 0%, #ddd7cf 45%, #a88b6c 80%, #6e5743 100%);
  }
  * { box-sizing: border-box; margin: 0; padding: 0; }
  html, body { width: 1200px; height: 3548px; overflow: hidden; }
  body { background: var(--stage); position: relative; font-family: "Montserrat", sans-serif; color: var(--ink); }
  .abs { position: absolute; }
  .page { position: absolute; background: var(--paper); }
  .photo { position: absolute; }
  .spine { position: absolute; width: 1px; background: rgba(0,0,0,0.08); }

  /* Cover */
  .brand { left: 306px; top: 128px; display: flex; align-items: center; gap: 12px; }
  .brand-mark { width: 50px; height: 50px; background: var(--brand-blue); }
  .brand-name { font-family: "Montserrat", sans-serif; font-weight: 600; font-size: 22px; color: var(--brand-blue); }
  .cover-kicker { left: 358px; top: 826px; font-size: 17px; font-weight: 500; }
  .cover-title { left: 356px; top: 836px; font-family: "Anton", sans-serif; font-size: 50px; line-height: 1.2; }
  .cover-sub { left: 358px; top: 892px; font-size: 17px; font-weight: 500; }
  .cover-year { left: 721px; top: 828px; font-family: "Oswald", sans-serif; font-weight: 700; font-size: 36px; letter-spacing: 8px; }

  /* Contents spread */
  .toc-item { position: absolute; right: 805px; text-align: right; color: #fff; }
  .toc-num { font-family: "Anton", sans-serif; font-size: 30px; line-height: 1; }
  .toc-label { font-size: 19px; font-weight: 500; margin-top: 18px; }
  .vertical { writing-mode: vertical-rl; transform: rotate(180deg); }
  .content-word { left: 468px; top: 1344px; font-family: "Anton", sans-serif; font-size: 78px; line-height: 1; height: 276px; }
  .welcome-kicker { left: 670px; top: 1318px; font-size: 20px; font-weight: 500; }
  .welcome-title { left: 668px; top: 1346px; font-family: "Anton", sans-serif; font-size: 56px; line-height: 1.1; }
  .accent-bar { left: 746px; top: 1438px; width: 8px; height: 42px; background: var(--ink); }
  .body-copy { font-size: 10.5px; line-height: 15px; font-weight: 500; }
  .welcome-copy { left: 773px; width: 250px; }

  /* Vision spread */
  .header-rule { position: absolute; height: 1px; background: var(--rule); }
  .header-rule span { position: absolute; right: 0; top: -1px; height: 3px; }
  .logo-slot { font-size: 11px; font-weight: 600; }
  .page-tag { font-size: 9px; font-weight: 700; }
  .feature-title { left: 847px; top: 2104px; font-family: "Anton", sans-serif; font-size: 20px; color: var(--brand-blue); }
  .feature-sub { left: 847px; top: 2137px; font-size: 10px; font-weight: 800; font-style: italic; }
  .vision-title { left: 667px; top: 2292px; font-family: "Anton", sans-serif; font-size: 29px; line-height: 40px; color: var(--brand-blue); }

  /* Quote spread */
  .on-blue { color: #fff; }
  .headline-vert { left: 170px; top: 3180px; font-family: "Anton", sans-serif; font-size: 34px; line-height: 1; height: 226px; color: #fff; }
  .subtitle-vert { left: 140px; top: 3330px; font-size: 19px; height: 76px; color: #fff; }
  .side-copy { left: 240px; top: 2962px; width: 128px; font-size: 9.6px; line-height: 15.3px; color: #fff; }
  .quote-box { left: 789px; top: 2892px; width: 298px; height: 535px; background: var(--quote-indigo); }
  .quote-mark { left: 780px; top: 2826px; font-family: "Anton", sans-serif; font-size: 110px; line-height: 1; color: #fff; }
  .quote-text { left: 837px; top: 2980px; width: 240px; font-size: 28px; line-height: 39.5px; font-weight: 400; color: #fff; letter-spacing: 0.5px; }
</style>
</head>
<body>

<!-- Cover -->
<section class="page" style="left:266px;top:79px;width:636px;height:889px;"></section>
<div class="abs brand"><span class="brand-mark"></span><span class="brand-name">Hearth &amp; Tile Works</span></div>
<div class="photo" role="img" aria-label="Cream shaker kitchen with range hood and stainless oven" style="left:303px;top:222px;width:596px;height:559px;background:var(--photo-kitchen);"></div>
<div class="abs" style="left:277px;top:452px;width:25px;height:331px;background:var(--brand-blue);"></div>
<p class="abs cover-kicker">specializing in</p>
<h1 class="abs cover-title">Kitchen &amp; bath</h1>
<p class="abs cover-sub">remodels</p>
<p class="abs cover-year">2020</p>
<div class="abs" style="left:713px;top:895px;width:119px;height:62px;background:var(--brand-blue);"></div>

<!-- Contents spread -->
<section class="page" style="left:87px;top:1052px;width:1007px;height:706px;"></section>
<div class="abs" style="left:95px;top:1059px;width:575px;height:692px;background:var(--brand-blue);"></div>
<div class="abs" style="left:440px;top:1271px;width:230px;height:422px;background:var(--paper);"></div>
<div class="abs" style="left:670px;top:1271px;width:417px;height:480px;background:var(--paper);"></div>
<div class="photo" role="img" aria-label="Charcoal grey kitchen cabinets with white island" style="left:670px;top:1059px;width:346px;height:210px;background:var(--photo-grey-kitchen);"></div>
<div class="abs" style="left:1029px;top:1059px;width:58px;height:210px;background:var(--brand-blue);"></div>
<div class="spine" style="left:590px;top:1059px;height:692px;"></div>

<nav>
  <div class="toc-item" style="top:1194px;"><div class="toc-num">01</div><div class="toc-label">Title Goes Here</div></div>
  <div class="toc-item" style="top:1296px;"><div class="toc-num">02</div><div class="toc-label">Another Title Here</div></div>
  <div class="toc-item" style="top:1405px;"><div class="toc-num">03</div><div class="toc-label">Page Headline Here</div></div>
  <div class="toc-item" style="top:1506px;"><div class="toc-num">04</div><div class="toc-label">Headline Here</div></div>
  <div class="toc-item" style="top:1615px;"><div class="toc-num">05</div><div class="toc-label">Another Headline</div></div>
</nav>
<h2 class="abs vertical content-word">CONTENT</h2>

<p class="abs welcome-kicker">Welcome To</p>
<h2 class="abs welcome-title">COMPANY</h2>
<div class="abs accent-bar"></div>
<p class="abs body-copy welcome-copy" style="top:1436px;">Lorem ipsum dolor sit amet, consectetur adipiscing elit. Sed molestie luctus est, quis malesuada purus volutpat nec. Sed fermentum tellus rhoncus lacus venenatis pellentesque. Vivamus nisl augue, lacinia sit amet augue sit amet, scelerisque porta elit. Aliquam erat volutpat.</p>
<p class="abs body-copy welcome-copy" style="top:1571px;">Donec pretium, tortor et laoreet cursus, magna magna interdum nulla, in aliquet tellus orci sit amet justo. Nullam justo nisl, semper ut lacinia at, tristique at purus. Quisque rhoncus odio a egestas vestibulum.</p>

<!-- Vision spread -->
<section class="page" style="left:87px;top:1898px;width:1007px;height:704px;"></section>
<div class="photo" role="img" aria-label="Bathroom with dark vanity, brass taps, mirrors and white tub" style="left:87px;top:1955px;width:540px;height:593px;background:var(--photo-bath);"></div>
<div class="spine" style="left:590px;top:1898px;height:704px;"></div>
<div class="header-rule" style="left:647px;top:1943px;width:325px;"><span style="width:103px;background:var(--brand-blue);"></span></div>
<p class="abs logo-slot" style="left:989px;top:1935px;">Your Logo</p>
<p class="abs page-tag" style="left:647px;top:1954px;color:var(--brand-blue);">Pages&nbsp; 08</p>

<div class="photo" role="img" aria-label="Small bathroom vanity photo" style="left:667px;top:2103px;width:156px;height:148px;background:var(--photo-bath);"></div>
<h3 class="abs feature-title">CONVALLIS JUSTOO</h3>
<p class="abs feature-sub">Magna Lobortisr</p>
<p class="abs body-copy" style="left:847px;top:2160px;width:200px;">Integer sed eleifend massa. Suspendisse hendrerit purus ac magna lobortis, sit amet convallis justo sagittis. Sed non dui libero. Quisque et sagittis ex, et dapibus mi. Maecenas eu faucibus leo.</p>
<div class="header-rule" style="left:667px;top:2274px;width:378px;"></div>
<h3 class="abs vision-title">Our Vision ,<br>Mission And<br>Value</h3>
<p class="abs body-copy" style="left:847px;top:2294px;width:200px;">Phasellus ut accumsan purus. Nam male suada lorem a velit pretium pellentesque eget eget magna. Aenean non massa lacinia, laoreet lacus nec, placerat velit. Proin tincidunt, magna et fermentum posuere, turpis velit pulvinar odio, volu tpat pulvinar velit lorem sed ex.</p>
<p class="abs body-copy" style="left:847px;top:2414px;width:200px;">Proin dictum arcu eu felis efficitur, ut iaculis risus accumsan. Donec odio arcu tempor eu imperdiet facilisis, pretium eget velit. Ut egestas nulla nibh, nec consectetur risus sagittis sit amet. Sed maximus, arcu nec porttitor mattiseget elit. Donec nec nisi arcu.</p>

<!-- Quote spread -->
<section class="page" style="left:87px;top:2758px;width:1007px;height:705px;"></section>
<div class="abs" style="left:95px;top:2765px;width:992px;height:691px;background:var(--brand-blue);"></div>
<div class="spine" style="left:590px;top:2765px;height:691px;background:rgba(255,255,255,0.15);"></div>

<div class="header-rule" style="left:135px;top:2806px;width:324px;background:rgba(255,255,255,0.45);"><span style="width:102px;background:#fff;"></span></div>
<p class="abs logo-slot on-blue" style="left:477px;top:2798px;">Your Logo</p>
<p class="abs page-tag on-blue" style="left:135px;top:2818px;">Pages&nbsp; 06</p>
<div class="header-rule" style="left:637px;top:2806px;width:324px;background:rgba(255,255,255,0.45);"><span style="width:102px;background:#fff;"></span></div>
<p class="abs logo-slot on-blue" style="left:989px;top:2798px;">Your Logo</p>
<p class="abs page-tag on-blue" style="left:637px;top:2816px;">Pages&nbsp; 07</p>

<div class="abs" style="left:220px;top:2882px;width:3px;height:520px;background:#fff;"></div>
<h2 class="abs vertical headline-vert">HEADLINE HERE</h2>
<p class="abs vertical subtitle-vert">Subtitle</p>
<p class="abs side-copy">Lorem ipsum dolor sit amet, consectetuer adipiscing elit, sed diam nonummy nibh euismod tincidunt ut laoreet dolore magna aliquam erat volutpat. Ut wisi enim ad minim veniam, quis nostrud exerci tation ullamcorper su scipit lobortis nisl ut aliquip ex ea commodo consequat. Duis autem vel eum iriure dolor in hendrerit in vulputate velit esse molestie co nsequat, vel illum dolore eu feugiat nulla facilisis at vero eros et accumsan et iusto odio dignissim qui blandit praesent luptatum zzril</p>

<div class="photo" role="img" aria-label="Bright kitchen with steel range, open shelves and marble island" style="left:396px;top:2892px;width:393px;height:535px;background:var(--photo-open-kitchen);"></div>
<div class="abs quote-box"></div>
<div class="abs quote-mark">&ldquo;</div>
<blockquote class="abs quote-text">Success isn’t just about what you ac­complish in your life; it’s about what you inspire others to do.</blockquote>

</body>
</html>
```